Martial Arts Website

Redevelopment of existing martial arts website.

The academy teaches traditional shaolin martial arts, including Shaolin Kung Fu, Wu Shu, Tai Chi, Qigong and Wing Chun and the site needs to reflect the traditional roots (eg, no tacky boxing imagery)

Existing website is www.copperlantern.com.au to get a feel for the desired color scheme (black, green and red). The exact colors can be tweaked though. Please only reuse the logo and font (Karate) - there isnt anything else from the current design that needs to remain.

The current website includes links to a ClipHarbor channel that includes demonstrations of the training conducted to better guide the design.

The new website site map will be:
1. Home
2. Programs - summary page describing each form of training
a. Tiny Otters
b. Kids Kung Fu
c. Youth Kung Fu
d. Adults Kung Fu
e. Wing Chun
f. Tai Chi & Qigong
g. Weaponry Classes
h. 72 Arts of Shaolin Conditioning Program
i. Acrobatics and Wu Shu
j. Fitness Boxing
3. Timetable
4. Coaches - summary page describing all coaches
a. Sifu (Master)
b. Sihing Kit
c. Sihing Sam
d. Sihing Marcus
X. ... up to 10 or so coaches
5. Member Zone
6. Contact Us
Updates

Logo now attached to brief - sorry I only have it in PDF

Just to clarify, I am only expecting a PSD design - no HTML required

Reason: Thanks for the designs, we love a lot of them just require a little extra time to tweak the designs and establish the potential. Thanks for your understanding and efforts.

Target Market(s)

Parents, teenagers, young adults, adults, elderly

Industry/Entity Type

Training

Requirements
Must have
• Chinese kung fu dragon imagery throughout the background
Links to Chatterly and ClipHarbor channel
Promo/icon in the header "Try 2 free classes now"
Home page should include an embedded ClipHarbor video

```html
<!DOCTYPE html>
<html lang="en">
<head>
<meta charset="utf-8">
<title>Copper Lantern Martial Arts Academy</title>
<link href="https://fonts.googleapis.com/css2?family=Ubuntu:wght@400;500&family=Lato:wght@400;700&display=swap" rel="stylesheet">
<style>
:root{
  --bg:#1c1c1c;
  --bg-top:#2a2a2a;
  --panel:#0c0c0c;
  --panel-soft:#1e1e1e;
  --green:#1fc41f;
  --green-dark:#0f7d0f;
  --green-text:#2bd62b;
  --nav-text:#0d2a0d;
  --white:#ffffff;
  --grey:#bdbdbd;
  --line:#3a3a3a;
}
*{margin:0;padding:0;box-sizing:border-box}
html,body{width:845px;height:1200px;overflow:hidden}
body{background:linear-gradient(var(--bg-top),var(--bg) 300px);font-family:"Lato",sans-serif;color:var(--white);position:relative}
.site-frame{position:absolute;left:12px;top:87px;width:821px;height:928px;background:var(--panel);border-radius:4px}
.main-nav{position:absolute;left:21px;top:95px;width:801px;height:54px;background:linear-gradient(#3fd83f,var(--green) 50%,var(--green-dark));border-radius:3px}
.nav-link{position:absolute;top:22px;font-family:"Ubuntu",sans-serif;font-size:12.5px;color:var(--nav-text);text-transform:uppercase}
.nav-link.small{font-size:11px;top:24px}
.nav-link.active{color:var(--green-text)}
.programs-tab{position:absolute;left:94px;top:8px;width:95px;height:46px;background:var(--panel);border-radius:6px 6px 0 0}
.dropdown{position:absolute;left:115px;top:147px;width:213px;height:105px;background:var(--panel);border-radius:0 0 6px 6px;z-index:3}
.dropdown a{position:absolute;font-family:"Ubuntu",sans-serif;font-size:10.5px;color:var(--green-text);text-decoration:none;white-space:nowrap}
.brand-badge{position:absolute;left:334px;top:21px;width:140px;height:140px;border-radius:50%;background:#061006;border:6px solid var(--green);display:flex;align-items:center;justify-content:center;text-align:center;font-family:"Ubuntu",sans-serif;font-size:15px;color:var(--green-text);line-height:1.2;z-index:4}
.hero{position:absolute;left:22px;top:151px;width:799px;height:297px;background:linear-gradient(180deg,#6d6a6a 0%,#c9c2bd 35%,#d59077 70%,#b97058 100%);border-radius:2px}
.intro{position:absolute;left:38px;top:469px;width:519px}
h1,h2{font-family:"Ubuntu",sans-serif;font-weight:400;color:var(--green-text)}
.intro h1{font-size:14px;margin-bottom:6px}
.intro p{font-size:9.6px;line-height:14.8px;text-align:justify;margin-bottom:4px}
.program-list{margin-top:14px}
.program-list p{font-size:8.4px;line-height:14.5px;text-align:left;margin-bottom:10px}
.program-list b{font-family:"Ubuntu",sans-serif;font-weight:400;color:var(--green-text);font-size:11px}
.classes-title{position:absolute;left:36px;top:820px;font-size:14px}
.classes-table{position:absolute;left:34px;top:845px;width:539px;height:153px;background:linear-gradient(#2a2a2a,#181818);border-radius:3px;display:grid;grid-template-columns:142px 144px 253px;grid-template-rows:52px 42px 59px}
.classes-table div{font-size:10.5px;line-height:15px;padding:12px 0 0 25px;border-right:1px solid var(--line);border-bottom:1px solid var(--line)}
.classes-table div:nth-child(3n){border-right:none;padding-left:25px}
.classes-table div:nth-child(n+7){border-bottom:none}
.sidebar{position:absolute;left:587px;top:452px;width:228px;height:546px;background:var(--panel-soft);border-radius:4px}
.sidebar h2{font-size:14px}
.news{position:absolute;left:16px;top:17px;width:206px}
.news-item{margin-top:11px}
.news-date{font-size:9px;font-weight:700;margin-bottom:6px}
.news-text{font-size:8.5px;line-height:14.8px;color:var(--green-text)}
.box{position:absolute;left:9px;width:213px;background:var(--panel);border-radius:6px;border:1px solid #2a2a2a}
.signup{top:279px;height:90px}
.signup h2{position:absolute;left:11px;top:10px}
.email-field{position:absolute;left:12px;top:36px;width:170px;height:24px;border-radius:12px 0 0 12px;background:linear-gradient(var(--green),var(--green-dark));font-size:9px;font-style:italic;color:#0b4a0b;padding:6px 0 0 12px}
.go-btn{position:absolute;left:176px;top:33px;width:30px;height:30px;border-radius:50%;background:#000;border:1.5px solid var(--green);font-family:"Ubuntu",sans-serif;font-size:12px;text-align:center;line-height:27px}
.social{top:375px;height:90px}
.social h2{position:absolute;left:12px;top:13px}
.social-links{position:absolute;left:18px;top:40px;display:flex;gap:14px}
.social-links span{display:flex;align-items:center;gap:4px;font-size:9.5px;color:var(--white)}
.social-links i{display:block;width:12px;height:12px;background:var(--green)}
.footer-nav{position:absolute;top:1038px;font-size:9.8px;list-style:none}
.footer-nav li{height:25px;padding-left:13px;position:relative}
.footer-nav li::before{content:"";position:absolute;left:0;top:3px;border-left:5px solid #8a8a8a;border-top:3.5px solid transparent;border-bottom:3.5px solid transparent}
.footer-badge{position:absolute;left:647px;top:1029px;width:100px;height:100px;border-radius:50%;background:#061006;border:4px solid var(--green);display:flex;align-items:center;justify-content:center;text-align:center;font-family:"Ubuntu",sans-serif;font-size:11px;color:var(--green-text)}
.copyright{position:absolute;left:40px;top:1165px;font-size:9px;color:#9a9a9a}
</style>
</head>
<body>
<div class="site-frame"></div>

<nav class="main-nav">
  <div class="programs-tab"></div>
  <span class="nav-link" style="left:42px">Home</span>
  <span class="nav-link active" style="left:110px">Programs</span>
  <span class="nav-link" style="left:205px">Timetable</span>
  <span class="nav-link small" style="left:501px">Coaches</span>
  <span class="nav-link small" style="left:575px">Member Zone</span>
  <span class="nav-link small" style="left:679px">Contact Us</span>
</nav>

<div class="dropdown">
  <a style="left:18px;top:10px">Tiny Otters</a>
  <a style="left:18px;top:32px">Kids Kung Fu</a>
  <a style="left:18px;top:54px">Youth Kung Fu</a>
  <a style="left:18px;top:76px">Adults Kung Fu</a>
  <a style="left:110px;top:10px">Wing Chun</a>
  <a style="left:110px;top:32px">Tai Chi &amp; Qigong</a>
  <a style="left:110px;top:54px">Weaponry Classes</a>
  <a style="left:110px;top:76px">72 Arts of Shaolin</a>
</div>

<div class="brand-badge">Copper<br>Lantern</div>

<div class="hero" role="img" aria-label="Photo of a kung fu master leading a tai chi class of students in white uniforms in a sports hall"></div>

<section class="intro">
  <h1>Welcome to Copper Lantern Martial Arts Academy - NSW Australia</h1>
  <p>Lorem ipsum dolor sit amet, consectetuer adipiscing elit. Nam cursus. Morbi ut mi. Nullam enim leo, egestas id, condimentum at, laoreet mattis, massa. Sed eleifend nonummy diam. Praesent mauris ante, elementum et, bibendum at, posuere sit amet, nibh. Duis tincidunt lectus quis dui viverra vestibulum.</p>
  <p>Suspendisse vulputate aliquam dui. Nulla elementum dui ut augue. Aliquam vehicula mi at mauris. Maecenas placerat, nisl at consequat rhoncus, sem nunc gravida justo, quis eleifend arcu velit quis lacus. Morbi magna magna, tincidunt a, mattis non, imperdiet vitae, tellus. Sed odio est, auctor ac, sollicitudin in, consequat vitae, orci. Fusce id felis. Vivamus sollicitudin metus eget eros.</p>
  <div class="program-list">
    <p><b>Tiny Otters</b> – ages 4 to 6. A specialised martial arts program for ages 4 to 6.</p>
    <p><b>Kids Kung Fu</b> – ages 6 to 11. Practical, Responsible Instruction. Plus, we specialize in powerful character development skills in a positive environment. Kids learn self defence NOT fighting, anti bullying techniques.</p>
    <p><b>Youth Kung Fu</b> – ages 11 to 15. The ultimate way to Build Confidence, Self-Esteem, Self-Discipline, and Athletic Skills, while learning self defence in a tradition style Martial Arts.</p>
    <p><b>Adults Shaolin Kung Fu</b> - ages 15 &amp; over. Self defence utilizing great range of punches, kicks, joint-locking, throwing and grappling techniques. The class utilizes traditional training methods designed to develop a sound mind and body.</p>
    <p><b>Wing Chun Kung Fu</b> – ages 13 &amp; over. Authentic Wing Chun Kung Fu by Harbour Wing Chun in the direct lineage to Lin Hao (World famous Wing Chun Master). Effective, direct, efficient Self Defence.</p>
  </div>
</section>

<h2 class="classes-title">Our Classes</h2>
<div class="classes-table">
  <div>Tiny Otters<br>Ages 4 to 6</div>
  <div>Adults Kung Fu<br>Ages 15 &amp; over</div>
  <div>Weaponry Classes<br>Ages 5 &amp; over</div>
  <div>Kids Kung Fu<br>Ages 6 to 11</div>
  <div>Wing Chun<br>Ages 13 &amp; over</div>
  <div>72 Arts of Shaolin<br>Conditioning Program</div>
  <div>Youth Kung Fu<br>Ages 11 to 15</div>
  <div>Tai Chi &amp; Qigong<br>All ages</div>
  <div>Performance Team<br>Acrobatics &amp; Wu Shu</div>
</div>

<aside class="sidebar">
  <div class="news">
    <h2>News &amp; Updates</h2>
    <div class="news-item"><div class="news-date">18.2012.2012</div><div class="news-text">Lorem ipsum dolor sit amet, consectetuer adipiscing elit. Nam cursus. Morbi ut mi. Nullam enim leo, egestas id.</div></div>
    <div class="news-item"><div class="news-date">18.2012.2012</div><div class="news-text">Lorem ipsum dolor sit amet, consectetuer adipiscing elit. Nam cursus. Morbi ut mi. Nullam enim leo, egestas id.</div></div>
    <div class="news-item"><div class="news-date">18.2012.2012</div><div class="news-text">Lorem ipsum dolor sit amet, consectetuer adipiscing elit. Nam cursus. Morbi ut mi. Nullam enim leo, egestas id.</div></div>
  </div>
  <div class="box signup">
    <h2>Newsletters Sign Up</h2>
    <div class="email-field">type email address</div>
    <div class="go-btn">Go</div>
  </div>
  <div class="box social">
    <h2>Social Media</h2>
    <div class="social-links">
      <span><i></i>ClipHarbor</span>
      <span><i></i>Chatterly</span>
    </div>
  </div>
</aside>

<ul class="footer-nav" style="left:39px"><li>Home</li><li>Programs</li><li>Timtable</li><li>Coaches</li></ul>
<ul class="footer-nav" style="left:137px"><li>Support</li><li>FAQ</li><li>Newsletters</li><li>Social Media</li></ul>
<ul class="footer-nav" style="left:249px"><li>Tiny Otters</li><li>Kids Kung Fu</li><li>Youth Kung Fu</li><li>Adults Kung Fu</li></ul>
<ul class="footer-nav" style="left:377px"><li>Wing Chun</li><li>Tai Chi &amp; Qigong</li><li>Weaponry Classes</li><li>72 Arts of Shaolin</li></ul>

<div class="footer-badge">Copper<br>Lantern</div>

<p class="copyright">© 2012 Company Name &nbsp;|&nbsp; All right reserved</p>
</body>
</html>
```